MRT Property - Business Cards

Looking for a business card & general letterhead, signage etc design for our new logo.

Colours:
000a20
0056a2
00b5ef
0088ce
68cef2

Fonts:
Poppins
Karla

Please keep look and feel of new brand - example in the zip package I sent.

```html
<!DOCTYPE html>
<html lang="en">
<head>
<meta charset="utf-8">
<title>MRT Property – Business Cards</title>
<link href="https://fonts.googleapis.com/css2?family=Poppins:wght@400;600;700&display=swap" rel="stylesheet">
<style>
  :root {
    --ink: #000a20;
    --brand-blue: #0056a2;
    --sky: #00b5ef;
    --mid-blue: #0088ce;
    --pale-sky: #68cef2;
    --white: #ffffff;
    --stage: #17181b;
  }
  * { margin: 0; padding: 0; box-sizing: border-box; }
  html, body { width: 1200px; height: 900px; overflow: hidden; }
  body {
    background: var(--stage);
    font-family: "Poppins", sans-serif;
    position: relative;
  }
  .card {
    position: absolute;
    left: 320px;
    width: 560px;
    height: 320px;
    border-radius: 22px;
    overflow: hidden;
    box-shadow: 0 14px 30px rgba(0,0,0,.5);
  }
  .card-front { top: 100px; background: var(--brand-blue); }
  .card-back  { top: 480px; }
  .card-art { position: absolute; inset: 0; width: 100%; height: 100%; display: block; }

  .contact {
    position: absolute;
    left: 30px;
    top: 96px;
    color: var(--white);
  }
  .contact-name {
    font-weight: 700;
    font-size: 24px;
    letter-spacing: 1px;
    text-transform: uppercase;
    color: var(--sky);
    line-height: 1.1;
  }
  .contact-role {
    font-size: 14px;
    margin: 2px 0 12px;
  }
  .contact-list { list-style: none; font-size: 13.5px; line-height: 1.45; }
  .contact-list li { display: flex; align-items: center; gap: 7px; }
  .contact-list svg { width: 11px; height: 11px; flex: none; }
  .contact-address { font-size: 13.5px; line-height: 1.45; margin-top: 4px; font-style: normal; }

  .brand-name {
    position: absolute;
    font-family: "Poppins", sans-serif;
    font-weight: 600;
    white-space: nowrap;
  }
  .card-front .brand-name { right: 30px; top: 128px; font-size: 30px; color: var(--brand-blue); }
  .card-back .brand-name { right: 36px; bottom: 34px; font-size: 28px; color: var(--white); }
</style>
</head>
<body>
  <section class="card card-front">
    <svg class="card-art" viewBox="0 0 560 320" aria-hidden="true">
      <rect width="560" height="320" fill="var(--brand-blue)"/>
      <path d="M130 0 C225 0 265 100 300 180 C345 265 450 300 560 292 L560 0 Z" fill="var(--mid-blue)" transform="translate(-8,18)"/>
      <path d="M130 0 C225 0 265 100 300 180 C345 265 450 300 560 292 L560 0 Z" fill="var(--white)" transform="translate(-5,11)"/>
      <path d="M130 0 C225 0 265 100 300 180 C345 265 450 300 560 292 L560 0 Z" fill="var(--sky)" transform="translate(-3,7)"/>
      <path d="M130 0 C225 0 265 100 300 180 C345 265 450 300 560 292 L560 0 Z" fill="var(--white)"/>
    </svg>
    <div class="contact">
      <h1 class="contact-name">Dana Whitlow</h1>
      <p class="contact-role">Founder &amp; Principal</p>
      <ul class="contact-list">
        <li><svg viewBox="0 0 12 12"><path d="M3 1 L5 4 L4 5 Q5 7 7 8 L8 7 L11 9 L10 11 Q4 11 1 3 Z" fill="var(--sky)"/></svg>+1- 555-014-2290</li>
        <li><svg viewBox="0 0 12 12"><rect x="1" y="2.5" width="10" height="7" fill="none" stroke="var(--sky)" stroke-width="1.2"/><path d="M1 2.5 L6 7 L11 2.5" fill="none" stroke="var(--sky)" stroke-width="1.2"/></svg>info@mrtproperty.com</li>
        <li><svg viewBox="0 0 12 12"><circle cx="6" cy="6" r="5" fill="var(--sky)"/><path d="M1 6 H11 M6 1 Q3 6 6 11 M6 1 Q9 6 6 11" fill="none" stroke="var(--brand-blue)" stroke-width=".8"/></svg>www.mrtproperty.com</li>
      </ul>
      <address class="contact-address">4120 North Harbor Lane<br>#12, Suite Riverton</address>
    </div>
    <p class="brand-name">MRT Property</p>
  </section>

  <section class="card card-back">
    <svg class="card-art" viewBox="0 0 560 320" role="img" aria-label="Repeating brand mark pattern in tonal blues">
      <defs>
        <linearGradient id="backTone" x1="0" y1="0" x2="1" y2="1">
          <stop offset="0" stop-color="#0a63b8"/>
          <stop offset="1" stop-color="var(--brand-blue)"/>
        </linearGradient>
      </defs>
      <rect width="560" height="320" fill="url(#backTone)"/>
    </svg>
    <p class="brand-name">MRT Property</p>
  </section>
</body>
</html>
```